BRELWINCare.co.uk - Mental Health Clinic for Child and Adolescents

Updated 29/01/2018***
I am not sure you guys are getting the idea regards to the opening page / homescreen layout. Can you look at the new images I have uploaded (page 5, 6 and 7) These are some of the layouts I like but to incorporate my chosen images, with the BRELWIN commissioner, buttons and a sliding header bar.
I have written a strong brief, I am looking for a website, preferably wordpress as i know they are easy to maintain. I am looking for a one page site, with the top / opening page being full screen image with drop down categories. I have made a rough design, see full brief in word doc attached, there is some freedom to play around with the design aspect but it will need to relay all the content provided. I like a minimal feel. I have also attached some images that may be useful, but will need a new logo for BRELWIN Care. I have attached some logo idea's, it is up to you decide whether you want to use them.
I would prefer the homepage as full screen image, and the categories offered as a drop down or over the main image.
I have also attached linked to some competitors websites:
https://www.vorimant-health.co.uk/
http://www.qlbn.org.uk/
Industry/Entity Type
Clinic
Number of Pages Required
1 page
Font styles to use
Look and feel
Each slider illustrates characteristics of the customer's brand and the style your logo design should communicate.

```html
<!DOCTYPE html>
<html lang="en">
<head>
<meta charset="utf-8">
<title>Our Services – BRELWIN Care</title>
<link rel="stylesheet" href="https://fonts.googleapis.com/css2?family=Open+Sans:wght@300;400;600;700&display=swap">
<style>
  :root {
    --ink: #1f2a2e;
    --heading: #26363b;
    --accent: #19d3e0;
    --panel-grey: #e6e6e6;
    --panel-light: #efefef;
    --edge: #2b3a40;
    --white: #ffffff;
  }
  * { margin: 0; padding: 0; box-sizing: border-box; }
  html, body { width: 1200px; height: 1200px; overflow: hidden; background: var(--white); }
  body { font-family: "Open Sans", Arial, sans-serif; color: var(--ink); position: relative; }

  .page-edge { position: absolute; left: 0; top: 0; width: 4px; height: 1200px; background: var(--edge); }

  .services-intro { position: absolute; left: 4px; top: 0; width: 1196px; height: 240px; text-align: center; }
  .services-title { position: absolute; top: 34px; width: 100%; font-weight: 400; font-size: 30px; letter-spacing: 1px; color: var(--ink); }
  .services-title span { color: var(--accent); }
  .services-lead { position: absolute; top: 94px; width: 100%; font-size: 14px; line-height: 29px; color: var(--ink); }
  .services-lead strong { font-weight: 700; }

  .photo { position: absolute; }
  .photo-adhd { left: 4px; top: 240px; width: 576px; height: 570px;
    background: linear-gradient(135deg, #ecebe8 0%, #d9d4cc 40%, #c9b59c 70%, #8f9aa6 100%); }
  .photo-asd { left: 622px; top: 810px; width: 578px; height: 390px;
    background: linear-gradient(120deg, #cfc6b8 0%, #a7b2b8 40%, #d8cfc1 75%, #eef0ef 100%); }

  .panel { position: absolute; }
  .panel-adhd { left: 580px; top: 240px; width: 620px; height: 570px; background: var(--panel-grey); }
  .panel-asd { left: 4px; top: 810px; width: 618px; height: 390px; background: var(--panel-light); }

  .service-heading { position: absolute; font-weight: 700; font-size: 29px; color: var(--heading); line-height: 1; letter-spacing: 0.5px; }
  .service-rule { position: absolute; height: 2px; background: var(--heading); }
  .service-body { position: absolute; font-size: 17.5px; line-height: 28.8px; color: var(--ink); white-space: nowrap; }
  .offered-label { position: absolute; font-weight: 700; font-size: 17px; color: var(--ink); }
  .offered-list { position: absolute; list-style: none; font-size: 17.5px; line-height: 28.8px; color: var(--ink); }
  .offered-list li { position: relative; padding-left: 35px; }
  .offered-list li::before { content: "•"; position: absolute; left: 0; font-size: 13px; }

  .panel-adhd .service-heading { left: 44px; top: 32px; }
  .panel-adhd .service-rule { left: 42px; top: 68px; width: 508px; }
  .panel-adhd .service-body { left: 46px; top: 78px; }
  .panel-adhd .offered-label { left: 51px; top: 321px; }
  .panel-adhd .offered-list { left: 52px; top: 349px; }

  .panel-asd .service-heading { left: 51px; top: 42px; }
  .panel-asd .service-rule { left: 50px; top: 80px; width: 509px; }
  .panel-asd .service-body { left: 53px; top: 93px; }
  .panel-asd .offered-label { left: 57px; top: 335px; }
  .panel-asd .offered-list { left: 58px; top: 363px; }
</style>
</head>
<body>
  <div class="page-edge"></div>

  <header class="services-intro">
    <h1 class="services-title">OUR <span>SERVICES</span></h1>
    <p class="services-lead"><strong>THE TEAM</strong> at BRELWIN are professional and passion driven individuals who help children and adolescent with disorder for<br>proper consultation and diagnostic. They make a difference for people.</p>
  </header>

  <div class="photo photo-adhd" role="img" aria-label="Photo of a clinician with a clipboard talking with a teenage boy in a bright room"></div>
  <section class="panel panel-adhd">
    <h2 class="service-heading">ADHD</h2>
    <div class="service-rule"></div>
    <p class="service-body">We have a multidisciplinary team that has been selected<br>due to their vast experience and reputation of being<br>some of the best in their field. The team consists of a<br>Clinical Psychologist, Consultant Psychiatrist and Nurse<br>who will work collaboratively to provide a robust, thor-<br>ough and highly accurate assessment.&nbsp; Should your child<br>need post treatment, we will recommend and offer sup-<br>port that is best suited to the child and family.</p>
    <h3 class="offered-label">Services offered are:</h3>
    <ul class="offered-list">
      <li>Service 1</li><li>Service 2</li><li>Service 3</li><li>Service 4</li><li>Service 5</li><li>Service 6</li>
    </ul>
  </section>

  <section class="panel panel-asd">
    <h2 class="service-heading">Autism (ASD)</h2>
    <div class="service-rule"></div>
    <p class="service-body">We have a multidisciplinary team that has been selected<br>due to their vast experience and reputation of being<br>some of the best in their field. The team consists of an<br>Assistant Psychologist, Clinical Psychologist, Consultant<br>Psychiatrist and a Nurse who will work collaboratively to<br>provide a robust, thorough and highly accurate assess-<br>ment.&nbsp; Should your child need post treatment, we will rec-<br>ommend and offer support that is best suited to the child</p>
    <h3 class="offered-label">Services offered are:</h3>
    <ul class="offered-list">
      <li>Service 1</li>
    </ul>
  </section>
  <div class="photo photo-asd" role="img" aria-label="Photo of a smiling clinician sitting on a sofa with a young girl"></div>
</body>
</html>
```